Business Card Design Project - del varosi group

dear Sirs

we need business card design for our group ( DEL Varosi Group ) , i have got the Logo design of our group from pixel harbor in previous , so all need details relating to our group i think available with you, as well as the the chosen logo design

we hope to provide us with business card logo that to be appropaite and satisfactory to us .

thanks

note : logo design of our group is attached .
Updates

Reason: please extend the deadline of my project for additional 15 days because i didn't received appropriate design for our gruop yet . kindly beaware that i have received 77 design till now , supossed to send me 200-250 design at least . thanks

Target Market(s)

contents

name : Kerem EL Nadiri

position : Operation Manager

Industry/Entity Type

Business

Requirements
Must have

• person name

group logo
Nice to have
• logo color matching with back background

```html
<!DOCTYPE html>
<html lang="en">
<head>
<meta charset="utf-8">
<title>DEL Varosi Group – Business Card</title>
<link href="https://fonts.googleapis.com/css2?family=PT+Sans:wght@400;700&display=swap" rel="stylesheet">
<style>
  :root {
    --backdrop: #b38a2c;
    --paper: #ffffff;
    --brand-blue: #0d4f91;
    --panel-light: #0b74c0;
    --panel-dark: #0a4c8a;
    --divider-gold: #c9a24a;
    --ink-light: #ffffff;
  }
  * { margin: 0; padding: 0; box-sizing: border-box; }
  html, body {
    width: 1200px; height: 686px; overflow: hidden;
    background: var(--backdrop);
    font-family: "PT Sans", sans-serif;
  }
  .canvas { position: relative; width: 1200px; height: 686px; }

  .card {
    position: absolute;
    background: var(--paper);
    box-shadow: 1px 2px 3px rgba(0,0,0,0.35);
  }
  .card--front { left: 55px; top: 156px; width: 524px; height: 299px; display: flex; }
  .card--back  { left: 609px; top: 249px; width: 523px; height: 299px;
                 display: flex; align-items: center; justify-content: center; }

  .front__logo-side {
    width: 280px; height: 100%;
    display: flex; align-items: center; justify-content: center;
  }
  .front__divider { width: 4px; height: 100%; background: var(--divider-gold); }
  .front__info {
    flex: 1; height: 100%; position: relative;
    background:
      linear-gradient(180deg, rgba(255,255,255,0) 0 55%, rgba(0,0,0,0.06) 55% 100%),
      radial-gradient(ellipse 120% 80% at 40% 0%, var(--panel-light), var(--panel-dark) 80%);
    color: var(--ink-light);
    padding: 54px 0 0 37px;
  }

  .wordmark {
    display: flex; align-items: center; gap: 8px;
    color: var(--brand-blue); font-weight: 700; letter-spacing: 0.5px;
    white-space: nowrap; text-transform: uppercase;
  }
  .wordmark__mark { background: var(--brand-blue); flex: none; }
  .wordmark--small { font-size: 22px; }
  .wordmark--small .wordmark__mark { width: 14px; height: 14px; }
  .wordmark--large { font-size: 31px; gap: 11px; }
  .wordmark--large .wordmark__mark { width: 19px; height: 19px; }

  .person__name { font-size: 17px; font-weight: 700; line-height: 1; }
  .person__role { font-size: 11px; font-weight: 700; margin-top: 7px; }

  .contact { list-style: none; margin-top: 22px; font-size: 12.5px; }
  .contact li { display: flex; align-items: center; gap: 3px; height: 18.5px; }
  .contact svg { width: 11px; height: 11px; fill: var(--ink-light); flex: none; }

  .address { margin-top: 12px; font-size: 12.5px; line-height: 16px; }
</style>
</head>
<body>
<div class="canvas">

  <section class="card card--front">
    <div class="front__logo-side">
      <div class="wordmark wordmark--small"><span class="wordmark__mark"></span>DEL Varosi Group</div>
    </div>
    <div class="front__divider"></div>
    <div class="front__info">
      <p class="person__name">Kerem EL Nadiri</p>
      <p class="person__role">Operation Manager</p>
      <ul class="contact">
        <li><svg viewBox="0 0 12 12"><path d="M2.5 1l2 2.2-1 1.3c.7 1.5 1.8 2.6 3.2 3.3l1.3-1 2.2 2-1 1.7C5 10.3 1.6 7 .8 2z"/></svg>(TF)123-456-7890</li>
        <li><svg viewBox="0 0 12 12"><path d="M2.5 1l2 2.2-1 1.3c.7 1.5 1.8 2.6 3.2 3.3l1.3-1 2.2 2-1 1.7C5 10.3 1.6 7 .8 2z"/></svg>&nbsp;123-456-7890</li>
        <li><svg viewBox="0 0 12 12"><path d="M3 1h5v3H3zM1 5h10v5H1zm2 1.5v1h2v-1zm0 2v.8h6v-.8z"/></svg>123-456-7890</li>
        <li><svg viewBox="0 0 12 12"><path d="M0 2.5h12v7H0zm1 .8L6 7l5-3.7z" fill-rule="evenodd"/></svg>&nbsp;name@website.com</li>
        <li><svg viewBox="0 0 12 12"><circle cx="6" cy="6" r="5.5"/><path d="M6 .5v11M.5 6h11M2 3h8M2 9h8" stroke="#0a4c8a" stroke-width=".8" fill="none"/></svg>www.website.com</li>
      </ul>
      <p class="address">Street name City<br>State, zip code</p>
    </div>
  </section>

  <section class="card card--back">
    <div class="wordmark wordmark--large"><span class="wordmark__mark"></span>DEL Varosi Group</div>
  </section>

</div>
</body>
</html>
```